TK Homes - Stone Dorf Design

Looking for a double sides design, 1 side for my realestate and the other for home building. ( TK Homes on 1 side, Stone Dorf card on the other Side
Side 1 - Marek Tove ~ Vox Realty logo and Company ( the Property quarter )
Marek Tove
Marek@Marektove.example
IG - Marek_Bzq_Realtor
FB - marekt
Cell - 5558130467
3847 61 St Nw

Side 2
Marek Tove
5558130467
IG - Stonedorf_Bzq
Stonedorfdev@mailbox.example

Target Market(s)

Home buyers/ sellers

Industry/Entity Type

Home builders - Realestate

Contact Information for Business Card

Above

Requirements
Must have
• Black OR White background - my information -

```html
<!DOCTYPE html>
<html lang="en">
<head>
<meta charset="utf-8">
<title>TK Homes – Stone Dorf Design business cards</title>
<link rel="stylesheet" href="https://fonts.googleapis.com/css2?family=Tinos:wght@400;700&display=swap">
<style>
  :root {
    --backdrop: #2b2b2e;
    --card: #1f1f23;
    --card-relief: #2a2a30;
    --blue: #1a6fc4;
    --gold: #f2c43a;
    --white: #f4f4f4;
    --muted: #d8d8d8;
  }
  * { box-sizing: border-box; margin: 0; padding: 0; }
  html, body {
    width: 1200px; height: 780px; overflow: hidden;
    background: var(--backdrop);
    font-family: "Tinos", "Times New Roman", serif;
  }
  .canvas {
    position: relative; width: 1200px; height: 780px;
    display: flex; align-items: center; justify-content: center; gap: 40px;
  }
  .card {
    position: relative; width: 540px; height: 310px;
    background: var(--card); overflow: hidden;
    box-shadow: 0 10px 24px rgba(0,0,0,.45);
  }
  .brand {
    position: absolute; left: 36px; top: 30px;
    display: flex; align-items: center; gap: 10px;
    font-size: 34px; font-weight: 700; letter-spacing: .5px;
  }
  .brand-mark { width: 14px; height: 14px; }
  .realty .brand { color: var(--blue); }
  .realty .brand-mark { background: var(--gold); border-radius: 50%; }
  .builder .brand { color: var(--white); }
  .builder .brand-mark { background: var(--white); }

  .address { position: absolute; left: 38px; top: 86px; color: var(--white); font-size: 15px; }

  .contacts {
    position: absolute; left: 36px; list-style: none;
    color: var(--white); font-size: 14px; line-height: 20px;
  }
  .realty .contacts { top: 116px; }
  .builder .contacts { top: 96px; }
  .contacts li { display: flex; align-items: center; gap: 8px; }
  .contacts svg { width: 12px; height: 12px; flex: none; }
  .realty .contacts svg { fill: var(--blue); }
  .builder .contacts svg { fill: var(--white); }

  .relief {
    position: absolute; right: 70px; bottom: -22px;
    font-size: 118px; font-weight: 700; line-height: 1;
    color: var(--card-relief); white-space: nowrap;
  }

  .signature { position: absolute; right: 58px; top: 150px; text-align: right; }
  .builder .signature { top: 120px; }
  .signature .name { font-size: 30px; font-weight: 700; line-height: 1; }
  .signature .title { font-size: 15px; font-weight: 700; color: var(--white); margin-top: 4px; }
  .realty .name .first { color: var(--blue); }
  .realty .name .last { color: var(--gold); }
  .builder .name { color: var(--white); }

  .edge-bar { position: absolute; right: 0; width: 44px; height: 44px; }
  .realty .edge-bar { top: 150px; background: var(--gold); }
  .builder .edge-bar { top: 120px; background: var(--white); }
</style>
</head>
<body>
<main class="canvas">

  <section class="card realty" aria-label="TK Homes real estate card">
    <div class="brand"><span class="brand-mark"></span>TK Homes</div>
    <p class="address">3847 61 St Nw</p>
    <ul class="contacts">
      <li><svg viewBox="0 0 12 12"><path d="M3 0l2 3-1.3 1.2a7 7 0 0 0 4 4L9 7l3 2-1 2.5C5 12 0 7 .5 1z"/></svg>5558130467</li>
      <li><svg viewBox="0 0 12 12"><circle cx="6" cy="6" r="6"/></svg>marekt</li>
      <li><svg viewBox="0 0 12 12"><circle cx="6" cy="6" r="6"/></svg>Marek_Bzq_Realtor</li>
      <li><svg viewBox="0 0 12 12"><path d="M0 2h12v8H0z M0 2l6 4.5L12 2" stroke="#1f1f23" stroke-width="1"/></svg>Marek@Marektove.example</li>
      <li><svg viewBox="0 0 12 12"><circle cx="6" cy="6" r="6"/></svg>www.marektove.example</li>
    </ul>
    <div class="relief" aria-hidden="true">TK Homes</div>
    <div class="signature">
      <p class="name"><span class="first">Marek</span> <span class="last">Tove</span></p>
      <p class="title">Director</p>
    </div>
    <div class="edge-bar"></div>
  </section>

  <section class="card builder" aria-label="Stone Dorf home building card">
    <div class="brand"><span class="brand-mark"></span>Stone Dorf</div>
    <ul class="contacts">
      <li><svg viewBox="0 0 12 12"><path d="M3 0l2 3-1.3 1.2a7 7 0 0 0 4 4L9 7l3 2-1 2.5C5 12 0 7 .5 1z"/></svg>5558130467</li>
      <li><svg viewBox="0 0 12 12"><circle cx="6" cy="6" r="6"/></svg>Stonedorf_Bzq</li>
      <li><svg viewBox="0 0 12 12"><path d="M0 2h12v8H0z M0 2l6 4.5L12 2" stroke="#1f1f23" stroke-width="1"/></svg>Stonedorfdev@mailbox.example</li>
    </ul>
    <div class="relief" aria-hidden="true">Stone Dorf</div>
    <div class="signature">
      <p class="name">Marek Tove</p>
      <p class="title">Director</p>
    </div>
    <div class="edge-bar"></div>
  </section>

</main>
</body>
</html>
```